Brookmere Osteopathy flyer

I want a clean clear DL flyer (but also want an A4 poster) promoting a new Osteopathic business in a semi rural area in Tasmania (Australia).
It can have pictures like the examples attached to show people what Osteopathy is (its like Chiropractic and physiotherapy).
I am the sole practioner and am male, so any pictures would be best to be a white male if possible.
I've attached some wording, you can use all, or none of it
I don't have a phone number for the business yet
info@brookmereosteopathy.example
www.brookmereosteopathy.example
Target Market(s)
Australians, from tradies, professionals, babies to retired people
Industry/Entity Type
Health
Look and feel

```html
<!DOCTYPE html>
<html lang="en">
<head>
<meta charset="utf-8">
<title>Brookmere Osteopathy – Flyer</title>
<link href="https://fonts.googleapis.com/css2?family=Poppins:wght@400;500;600;700&display=swap" rel="stylesheet">
<style>
  :root{
    --orange:#f5923e;
    --navy:#062d44;
    --teal-navy:#0b4a6b;
    --blue:#1a95d2;
    --tick:#1a8fd0;
    --ink:#1c2430;
    --white:#ffffff;
    --backdrop:#ebe9ea;
  }
  *{box-sizing:border-box;margin:0;padding:0}
  html,body{width:930px;height:1200px;overflow:hidden;background:var(--backdrop);font-family:'Poppins',sans-serif}
  .flyer{
    position:absolute;left:40.5px;top:0;width:1120px;height:1583px;
    transform:scale(0.758);transform-origin:0 0;
    background:var(--white);overflow:hidden;color:var(--ink);
  }
  .abs{position:absolute}
  .brand{left:97px;top:110px;display:flex;align-items:center;gap:18px}
  .brand-dot{width:34px;height:34px;border-radius:50%;background:var(--blue)}
  .brand-name{font-size:30px;font-weight:600;color:var(--blue);line-height:1.15;width:200px}
  .hero-band{left:0;top:338px;width:1120px;height:411px;background:var(--orange)}
  .photo{background:linear-gradient(135deg,#d9a585,#8c5a45);border-radius:50%}
  .photo-main{left:540px;top:-57px;width:620px;height:620px;border:4px solid var(--white);
    background:linear-gradient(140deg,#2b2f36 0%,#c98e6c 45%,#e2b495 70%,#3a2c26 100%)}
  .photo-small{left:458px;top:302px;width:316px;height:316px;border:4px solid var(--white);
    background:linear-gradient(150deg,#b8c6d2 0%,#e9ecef 50%,#8e959c 100%)}
  .headline{left:97px;top:360px;line-height:.95}
  .headline .light{font-size:54px;font-weight:400;color:var(--white);display:block}
  .headline .bold{font-size:54px;font-weight:700;color:var(--white);display:block}
  .headline .big{font-size:88px;font-weight:700;color:var(--teal-navy);display:block;letter-spacing:-1px;line-height:.9}
  .tagline{left:97px;top:642px;font-size:33px;font-weight:600;color:var(--white);line-height:1.25}
  .reasons-pill{left:130px;top:749px;width:859px;height:74px;background:var(--navy);border-radius:0 0 14px 14px;
    display:flex;align-items:center;justify-content:center;color:var(--white);font-size:30px;font-weight:600;letter-spacing:.2px}
  .reasons{top:856px;list-style:none;font-size:21.5px;line-height:1.15}
  .reasons li{display:flex;gap:10px;margin-bottom:10px}
  .reasons svg{flex:none;margin-top:4px}
  .col1{left:95px}.col2{left:453px}.col3{left:763px}
  .divider{top:858px;height:122px;border-left:2px dotted #6b6b6b}
  .d1{left:411px}.d2{left:727px}
  .info-band{left:0;top:1165px;width:1120px;height:246px;background:var(--blue)}
  .photo-row{width:290px;height:290px;border:4px solid var(--white);top:1030px}
  .p1{left:96px;background:linear-gradient(135deg,#3d7fc4,#d69c7c 60%,#f0c4a6)}
  .p2{left:414px;background:linear-gradient(160deg,#e8e8e8,#2b3442 40%,#b87c5e 75%,#2a9b9e)}
  .p3{left:732px;background:linear-gradient(160deg,#222 0%,#d7a789 40%,#f2f2f2 100%)}
  .about{left:97px;top:1340px;width:950px;font-size:21px;color:var(--white);line-height:1.2}
  .about strong{font-weight:700}
  .footer{left:0;top:1411px;width:1120px;height:172px;background:var(--navy)}
  .contact{top:1436px;color:var(--white);font-size:23px;line-height:1.4;white-space:nowrap}
  .contact div{display:flex;align-items:center;gap:8px}
  .contact svg{flex:none}
  .contact .phone{font-weight:700;font-size:24px}
  .c-left{left:97px}.c-right{left:600px}
  .footer-rule{left:576px;top:1440px;height:62px;border-left:1.5px solid #8aa0ad}
</style>
</head>
<body>
<div class="flyer">
  <div class="abs brand"><span class="brand-dot"></span><span class="brand-name">Brookmere Osteopathy</span></div>

  <div class="abs hero-band"></div>
  <div class="abs photo photo-main" role="img" aria-label="Practitioner's hands treating a patient's upper back and shoulder"></div>
  <div class="abs photo photo-small" role="img" aria-label="Osteopath stretching a patient's leg on a treatment table"></div>

  <h1 class="abs headline">
    <span class="light">NATURAL</span>
    <span class="bold">HEALING</span>
    <span class="big">EXPERT</span>
    <span class="big">HANDS</span>
  </h1>
  <p class="abs tagline">Treating the root cause of pain with gentle,<br>effective osteopathic techniques.</p>

  <div class="abs reasons-pill">COMMON REASONS PEOPLE VISIT AN OSTEOPATH</div>

  <ul class="abs reasons col1">
    <li><svg width="18" height="18" viewBox="0 0 18 18"><circle cx="9" cy="9" r="9" fill="var(--tick)"/><path d="M5 9.3l2.6 2.5L13 6.5" stroke="#fff" stroke-width="2" fill="none"/></svg><span>Back / neck pain</span></li>
    <li><svg width="18" height="18" viewBox="0 0 18 18"><circle cx="9" cy="9" r="9" fill="var(--tick)"/><path d="M5 9.3l2.6 2.5L13 6.5" stroke="#fff" stroke-width="2" fill="none"/></svg><span>Headaches / migraines</span></li>
    <li><svg width="18" height="18" viewBox="0 0 18 18"><circle cx="9" cy="9" r="9" fill="var(--tick)"/><path d="M5 9.3l2.6 2.5L13 6.5" stroke="#fff" stroke-width="2" fill="none"/></svg><span>Joint and muscle pain</span></li>
    <li><svg width="18" height="18" viewBox="0 0 18 18"><circle cx="9" cy="9" r="9" fill="var(--tick)"/><path d="M5 9.3l2.6 2.5L13 6.5" stroke="#fff" stroke-width="2" fill="none"/></svg><span>Adhesive capsulitis<br>(frozen shoulder)</span></li>
  </ul>
  <div class="abs divider d1"></div>
  <ul class="abs reasons col2">
    <li><svg width="18" height="18" viewBox="0 0 18 18"><circle cx="9" cy="9" r="9" fill="var(--tick)"/><path d="M5 9.3l2.6 2.5L13 6.5" stroke="#fff" stroke-width="2" fill="none"/></svg><span>Pregnancy-related<br>discomfort</span></li>
    <li><svg width="18" height="18" viewBox="0 0 18 18"><circle cx="9" cy="9" r="9" fill="var(--tick)"/><path d="M5 9.3l2.6 2.5L13 6.5" stroke="#fff" stroke-width="2" fill="none"/></svg><span>Disc related issues</span></li>
    <li><svg width="18" height="18" viewBox="0 0 18 18"><circle cx="9" cy="9" r="9" fill="var(--tick)"/><path d="M5 9.3l2.6 2.5L13 6.5" stroke="#fff" stroke-width="2" fill="none"/></svg><span>Sciatica</span></li>
  </ul>
  <div class="abs divider d2"></div>
  <ul class="abs reasons col3">
    <li><svg width="18" height="18" viewBox="0 0 18 18"><circle cx="9" cy="9" r="9" fill="var(--tick)"/><path d="M5 9.3l2.6 2.5L13 6.5" stroke="#fff" stroke-width="2" fill="none"/></svg><span>Plantar fasciitis</span></li>
    <li><svg width="18" height="18" viewBox="0 0 18 18"><circle cx="9" cy="9" r="9" fill="var(--tick)"/><path d="M5 9.3l2.6 2.5L13 6.5" stroke="#fff" stroke-width="2" fill="none"/></svg><span>Tendonitis / Bursitis</span></li>
    <li><svg width="18" height="18" viewBox="0 0 18 18"><circle cx="9" cy="9" r="9" fill="var(--tick)"/><path d="M5 9.3l2.6 2.5L13 6.5" stroke="#fff" stroke-width="2" fill="none"/></svg><span>Tennis / Golfers elbow</span></li>
  </ul>

  <div class="abs info-band"></div>
  <div class="abs photo photo-row p1" role="img" aria-label="Deep tissue massage on a patient's back"></div>
  <div class="abs photo photo-row p2" role="img" aria-label="Osteopath treating a patient lying face down"></div>
  <div class="abs photo photo-row p3" role="img" aria-label="Hands supporting the back of a patient's neck"></div>

  <p class="abs about"><strong>Osteopaths</strong> use a combination of joint manipulation, targeted deep tissue massage and stretching to improve function, relieve pain and support the body’s ability to heal itself.</p>

  <div class="abs footer"></div>
  <div class="abs contact c-left">
    <div class="phone"><svg width="22" height="22" viewBox="0 0 22 22"><circle cx="11" cy="11" r="11" fill="var(--orange)"/><path d="M7.5 6c.6-.5 1.3-.4 1.6.2l.8 1.6c.2.5 0 1-.4 1.3l-.6.4c.5 1.3 1.4 2.3 2.7 2.8l.4-.6c.3-.4.8-.6 1.3-.4l1.6.8c.6.3.7 1 .2 1.6-.9 1.1-2.3 1.3-3.6.6-2-1.1-3.4-2.6-4.4-4.6-.7-1.3-.5-2.7.4-3.7z" fill="#fff"/></svg>033 555 010 2468</div>
    <div><svg width="22" height="22" viewBox="0 0 22 22"><circle cx="11" cy="11" r="11" fill="var(--orange)"/><rect x="5.5" y="7" width="11" height="8" rx="1" fill="#fff"/><path d="M5.8 7.4l5.2 4 5.2-4" stroke="var(--orange)" stroke-width="1.2" fill="none"/></svg>info@brookmereosteopathy.example</div>
  </div>
  <div class="abs footer-rule"></div>
  <div class="abs contact c-right">
    <div><svg width="22" height="22" viewBox="0 0 22 22"><circle cx="11" cy="11" r="11" fill="var(--orange)"/><circle cx="11" cy="11" r="5.5" stroke="#fff" stroke-width="1.4" fill="none"/><path d="M5.5 11h11M11 5.5c-2.5 3-2.5 8 0 11M11 5.5c2.5 3 2.5 8 0 11" stroke="#fff" stroke-width="1.2" fill="none"/></svg>www.brookmereosteopathy.example</div>
    <div><svg width="22" height="22" viewBox="0 0 22 22"><circle cx="11" cy="11" r="11" fill="var(--orange)"/><path d="M11 5a4 4 0 0 1 4 4c0 3-4 7.5-4 7.5S7 12 7 9a4 4 0 0 1 4-4z" fill="#fff"/><circle cx="11" cy="9" r="1.5" fill="var(--orange)"/></svg>24 Fernside Road, Brookmere</div>
  </div>
</div>
</body>
</html>
```